Stationary design for boutique production house

We need a stationary design for our production house, 'Lorno Productions' based in Singapore. We produce microfilms as well as podcasts, talkshows and events. Our logo is a stylized icon of our director, who is also the executive producer and host of our programs, Lorno. Our main company colors are Red, Black and white. We would like a clean, minimalist design incorporating our existing company logo that conveys a sense of urbanism and elegance.

Logo and font files are attached. f

Target Market(s)

We focus on lifestyle media rather than entertainment.

Industry/Entity Type

Boutique

Font styles to use
Serif
Sans Serif

Colors
ec1f27
ffffff
000000

Requirements
Must have
• Our company logo and at least one of our company colors.
Nice to have
• Our address and contact information.
Should not have
• Changes made to the company logo (using only certain parts of it is fine though)

```html
<!DOCTYPE html>
<html lang="en">
<head>
<meta charset="utf-8">
<title>Lorno Productions – Business Card</title>
<link href="https://fonts.googleapis.com/css2?family=Jost:wght@400;500&family=Libre+Baskerville&display=swap" rel="stylesheet">
<style>
  :root {
    --stage: #3a3a3a;
    --paper: #f7f7f7;
    --ink: #231f20;
    --ink-soft: #4a4a4a;
    --brand-red: #ec1f27;
    --card-dark: #262224;
    --card-dark-tone: #332e30;
    --white: #ffffff;
  }
  * { box-sizing: border-box; margin: 0; padding: 0; }
  html, body { width: 1200px; height: 768px; overflow: hidden; }
  body {
    background: var(--stage);
    font-family: "Jost", sans-serif;
    display: flex;
    align-items: center;
    justify-content: center;
    gap: 48px;
  }
  .card {
    width: 540px;
    height: 309px;
    position: relative;
    box-shadow: 0 8px 24px rgba(0,0,0,.35);
  }

  /* Back side */
  .card-back { background: var(--card-dark); overflow: hidden; }
  .back-pattern {
    position: absolute; inset: 0;
    background: linear-gradient(160deg, var(--card-dark-tone), var(--card-dark));
  }
  .back-brand {
    position: absolute;
    right: 48px; bottom: 70px;
    display: flex; align-items: center; gap: 10px;
    color: var(--white);
    font-size: 22px; font-weight: 500;
    letter-spacing: .04em;
  }
  .brand-dot {
    width: 12px; height: 12px; border-radius: 50%;
    background: var(--brand-red);
  }
  .back-web {
    position: absolute;
    right: 48px; bottom: 44px;
    color: #d8d8d8;
    font-family: "Libre Baskerville", serif;
    font-size: 13px;
  }

  /* Front side */
  .card-front { background: var(--paper); color: var(--ink-soft); }
  .front-brand {
    position: absolute;
    top: 62px; left: 0; right: 0;
    display: flex; justify-content: center; align-items: center; gap: 10px;
    color: var(--ink);
    font-size: 26px; font-weight: 500;
    letter-spacing: .04em;
  }
  .divider {
    position: absolute;
    top: 140px; left: 28px; right: 28px;
    border-top: 1px solid var(--ink-soft);
  }
  .person {
    position: absolute;
    top: 150px; left: 32px;
    line-height: 1.25;
  }
  .person-name { color: var(--ink); font-size: 18px; font-weight: 400; letter-spacing: .03em; }
  .person-title { color: var(--brand-red); font-size: 14px; letter-spacing: .03em; margin-bottom: 4px; }
  .person-address { font-size: 13px; font-style: normal; }

  .contact-list {
    position: absolute;
    right: 30px; bottom: 28px;
    list-style: none;
    font-size: 14px;
    line-height: 1.45;
    text-align: right;
  }
  .contact-list li { display: flex; justify-content: flex-end; align-items: center; gap: 10px; }
  .contact-icon { width: 13px; height: 13px; fill: var(--ink); }
</style>
</head>
<body>

  <section class="card card-back">
    <div class="back-pattern" role="img" aria-label="Faint repeated pattern of the Lorno Productions mark on a dark ground"></div>
    <div class="back-brand"><span class="brand-dot"></span>Lorno Productions</div>
    <div class="back-web">www.lorno.sg</div>
  </section>

  <section class="card card-front">
    <div class="front-brand"><span class="brand-dot"></span>Lorno Productions</div>
    <div class="divider"></div>

    <div class="person">
      <div class="person-name">MARA KWOK</div>
      <div class="person-title">CEO/FOUNDER</div>
      <address class="person-address">12 Keong Saik Road<br>Singapore 089128</address>
    </div>

    <ul class="contact-list">
      <li>6221 4087
        <svg class="contact-icon" viewBox="0 0 16 16" aria-hidden="true"><path d="M3 1l3 3-1.5 2c1 2 3 4 5 5L11.5 9.5l3 3-2 2.5C7 15 1 9 .5 3.5z"/></svg>
      </li>
      <li>9183 5526
        <svg class="contact-icon" viewBox="0 0 16 16" aria-hidden="true"><path d="M4 0h8v16H4zM5.5 2v10h5V2zM7 13.5h2v1H7z" fill-rule="evenodd"/></svg>
      </li>
      <li>6221 4090
        <svg class="contact-icon" viewBox="0 0 16 16" aria-hidden="true"><path d="M4 1h7l1 1v4H4zM1 7h14v6h-3v2H4v-2H1zM5 11v3h6v-3z" fill-rule="evenodd"/></svg>
      </li>
      <li>mara@lorno.sg
        <svg class="contact-icon" viewBox="0 0 16 16" aria-hidden="true"><path d="M0 3h16v10H0zM1.5 4.5L8 9l6.5-4.5v-.2H1.5z" fill-rule="evenodd"/></svg>
      </li>
    </ul>
  </section>

</body>
</html>
```